Copperleaf Balustrade Website Redesign

I want a fresh new design for my website. Original website
www.copperleafbalustrade-example.com. Will need to add additional photos for winning designer. Please use the basic layout for new design. Looking to get a more modern, functional site to attract new customer and ne bale to highlight past projects. Need it to be easy to navigate and get in touch with me for inquiries.

Target Market(s)

Builders and home owners in WA state

Industry/Entity Type

Building, Construction, Deck building

Coding

Coded - Design and coding required

Number of Pages Required

5+ page

Font styles to use
Sans Serif

Colors
0054AA
0677BA
7BADD7
CADEEF
E8F1F8
0094D4
00A9DD
6FCCEA
C7EBF8
E9F6FB
00AB8E
00BBA5
67D7C9
C6EFE9
E9F9F6
59FF00
82FF00
B8FF75
E3FFCB
F4FFEA

Requirements
Must have
• Will need to add more photos of completed projects
Nice to have
• Fresh take on old website, something modern
Should not have
• Nothing comes to mind

```html
<!DOCTYPE html>
<html lang="en">
<head>
<meta charset="utf-8">
<title>Copperleaf Balustrade – About</title>
<link href="https://fonts.googleapis.com/css2?family=Inter:wght@500;600;700;800&family=Jost:wght@400;500;600&display=swap" rel="stylesheet">
<style>
:root{
  --green:#0b6b3a;
  --green-bright:#2fa060;
  --green-soft:#9fd0bd;
  --ink:#111;
  --text:#2b2b2b;
  --tint:#e8f6f3;
  --footer:#000;
  --white:#fff;
}
*{margin:0;padding:0;box-sizing:border-box}
html,body{width:826px;height:1200px;overflow:hidden;background:var(--white)}
body{position:relative;font-family:'Jost',sans-serif;color:var(--text)}
.abs{position:absolute}

/* header */
.site-header{position:absolute;left:0;top:0;width:826px;height:63px;background:var(--white)}
.brand{position:absolute;left:39px;top:18px;display:flex;align-items:center;gap:7px}
.brand-mark{width:14px;height:14px;background:var(--green)}
.brand-name{font-family:'Jost',sans-serif;font-weight:500;font-size:15px;color:var(--green);letter-spacing:.2px}
.nav a{position:absolute;top:28px;font-family:'Inter',sans-serif;font-weight:600;font-size:9.5px;color:var(--ink);text-decoration:none;letter-spacing:.1px}
.nav a.active{color:var(--green)}
.nav a.cta{top:22px;left:726px;width:61px;height:24px;background:var(--green);color:var(--white);display:flex;align-items:center;justify-content:center}

/* hero */
.hero{position:absolute;left:0;top:63px;width:826px;height:237px;background:linear-gradient(100deg,#4f5a58 0%,#3a3f3d 40%,#6f7878 65%,#9a9e9c 100%)}
.hero h1{position:absolute;left:39px;top:103px;font-family:'Inter',sans-serif;font-weight:800;font-size:26px;color:var(--white)}

/* about */
.about-photo{position:absolute;left:39px;top:335px;width:347px;height:239px;background:linear-gradient(135deg,#4e7a45 0%,#a2643a 45%,#c6803f 70%,#6a4030 100%)}
.about-copy{position:absolute;left:427px;top:364px;width:360px}
.about-copy h2{font-family:'Inter',sans-serif;font-weight:700;font-size:17.5px;color:var(--green);margin-bottom:8px}
.about-copy p{font-size:9px;line-height:13.8px;margin-bottom:13.8px}

/* mission band */
.band{position:absolute;left:0;top:611px;width:826px;height:408px;background:var(--tint)}
.card{position:absolute;background:var(--white);border:1px solid var(--green-soft);text-align:center}
.card h3{font-family:'Inter',sans-serif;font-weight:700;font-size:17px;color:var(--green)}
.card p{font-size:9px;line-height:13.8px;margin-top:8px}
.mission{left:39px;top:646px;width:370px;height:138px;padding:33px 26px 0}
.vision{left:417px;top:646px;width:370px;height:138px;padding:33px 14px 0}
.values{left:39px;top:800px;width:748px;height:182px;padding-top:33px}
.value{position:absolute;top:76px;width:110px;margin-left:-55px;text-align:center}
.value .ring{width:51px;height:51px;border:1px solid var(--green-soft);border-radius:50%;margin:0 auto;display:flex;align-items:center;justify-content:center}
.value span{display:block;margin-top:13px;font-weight:600;font-size:9.5px;color:#222}

/* footer */
.site-footer{position:absolute;left:0;top:1019px;width:826px;height:181px;background:var(--footer);color:var(--white)}
.footer-brand{position:absolute;left:40px;top:36px;display:flex;align-items:center;gap:8px}
.footer-brand .brand-mark{width:18px;height:18px;background:var(--green-bright)}
.footer-brand .brand-name{font-size:19px;color:var(--green-bright);font-weight:500}
.footer-about{position:absolute;left:39px;top:85px;width:230px;font-size:9px;line-height:13.8px}
.footer-col h4{position:absolute;top:30px;font-family:'Inter',sans-serif;font-weight:600;font-size:9.5px;color:var(--green-bright)}
.footer-col ul{position:absolute;top:52px;list-style:none}
.footer-col li{font-size:9px;height:21px;display:flex;align-items:center;gap:8px}
.footer-col li::before{content:"";width:4px;height:4px;background:var(--green-bright);transform:rotate(45deg)}
.social{position:absolute;top:1073px;width:21px;height:21px;border-radius:50%;background:var(--green-bright)}
.footer-rule{position:absolute;left:0;top:149px;width:826px;height:1px;background:#444}
.copyright{position:absolute;left:0;top:158px;width:826px;text-align:center;font-size:9px}
</style>
</head>
<body>

<header class="site-header">
  <div class="brand"><div class="brand-mark"></div><div class="brand-name">Copperleaf Balustrade</div></div>
  <nav class="nav">
    <a style="left:406px">HOME</a>
    <a class="active" style="left:467px">ABOUT</a>
    <a style="left:533px">PRODUCT</a>
    <a style="left:612px">WHY CHOOSE US</a>
    <a class="cta">CONTACT</a>
  </nav>
</header>

<section class="hero" role="img" aria-label="Covered balcony with dark-framed glass railing beside trees">
  <h1>ABOUT</h1>
</section>

<div class="about-photo" role="img" aria-label="Wooden porch staircase with timber posts and black metal balusters"></div>
<section class="about-copy">
  <h2>ABOUT</h2>
  <p>At Copperleaf Balustrade, we believe that every outdoor space deserves the perfect blend of style, safety, and durability. Serving homeowners, builders, and commercial developers across the Washington State, we specialize in crafting custom railing systems designed to withstand the region’s unique climate while enhancing the beauty of your outdoor living spaces.</p>
  <p>With a focus on premium materials, expert craftsmanship, and exceptional customer service, Copperleaf Balustrade is proud to be the trusted partner for both residential and commercial railing projects. Whether you’re looking to complement a new deck, add a modern touch to your balcony, or create a secure and stunning barrier for a commercial space, we’ve got the perfect solution for you.</p>
</section>

<div class="band"></div>
<div class="card mission">
  <h3>MISSION</h3>
  <p>To enhance the beauty and safety of outdoor living spaces across Washington State by crafting exceptional, custom railing systems that are both stylish and resilient to the Pacific Northwest’s unique climate.</p>
</div>
<div class="card vision">
  <h3>VISION</h3>
  <p>To be the preferred choice for homeowners and businesses throughout Washington, recognized for our superior craftsmanship, exceptional customer service, and unwavering commitment to creating enduring and elegant railing systems</p>
</div>
<div class="card values">
  <h3>VALUES</h3>
  <div class="value" style="left:79px"><div class="ring"><svg width="22" height="22" viewBox="0 0 22 22" fill="none" stroke="#0b6b3a" stroke-width="1.2"><path d="M4 18l9-9M12 4l6 6-3 3-6-6z"/></svg></div><span>Craftsmanship</span></div>
  <div class="value" style="left:197px"><div class="ring"><svg width="22" height="22" viewBox="0 0 22 22" fill="none" stroke="#0b6b3a" stroke-width="1.2"><circle cx="11" cy="9" r="6"/><path d="M7 14l-2 6 3-1 2 2 1-5M15 14l2 6-3-1-2 2"/></svg></div><span>Quality</span></div>
  <div class="value" style="left:315px"><div class="ring"><svg width="22" height="22" viewBox="0 0 22 22" fill="none" stroke="#0b6b3a" stroke-width="1.2"><circle cx="11" cy="11" r="8"/><path d="M7 11l3 3 5-6"/></svg></div><span>Customer Focus</span></div>
  <div class="value" style="left:433px"><div class="ring"><svg width="22" height="22" viewBox="0 0 22 22" fill="none" stroke="#0b6b3a" stroke-width="1.2"><circle cx="11" cy="9" r="5.5"/><path d="M8.5 15h5M9 18h4"/></svg></div><span>Innovation</span></div>
  <div class="value" style="left:551px"><div class="ring"><svg width="22" height="22" viewBox="0 0 22 22" fill="none" stroke="#0b6b3a" stroke-width="1.2"><path d="M5 12a6 6 0 0 1 10-5l2 2M17 10a6 6 0 0 1-10 5l-2-2M17 5v4h-4M5 17v-4h4"/></svg></div><span>Sustainability</span></div>
  <div class="value" style="left:669px"><div class="ring"><svg width="22" height="22" viewBox="0 0 22 22" fill="none" stroke="#0b6b3a" stroke-width="1.2"><rect x="4" y="4" width="7" height="7"/><rect x="11" y="11" width="7" height="7"/></svg></div><span>Integrity</span></div>
</div>

<footer class="site-footer">
  <div class="footer-brand"><div class="brand-mark"></div><div class="brand-name">Copperleaf Balustrade</div></div>
  <p class="footer-about">we specialize in crafting custom railing systems designed to withstand the region’s unique climate while enhancing the beauty of your outdoor living spaces.</p>
  <div class="footer-col">
    <h4 style="left:347px">QUICK LINKS</h4>
    <ul style="left:349px"><li>Home</li><li>Product</li><li>Why Choose us</li><li>Contact</li></ul>
  </div>
  <div class="footer-col">
    <h4 style="left:499px">OUR PRODUCT</h4>
    <ul style="left:501px"><li>Aluminum Railings</li><li>Glass Railings</li><li>Cable Railings</li><li>Custom design</li></ul>
  </div>
  <div class="footer-col">
    <h4 style="left:678px;top:29px">CONNECT WITH US</h4>
  </div>
  <div class="footer-rule"></div>
  <p class="copyright">© Copyright 2024&nbsp; All Rights Reserved</p>
</footer>
<div class="social" style="left:678px" aria-label="Social link"></div>
<div class="social" style="left:706px" aria-label="Social link"></div>
<div class="social" style="left:733px" aria-label="Social link"></div>
<div class="social" style="left:760px" aria-label="Social link"></div>

</body>
</html>
```